New Newspaper Ad Design Project

We need an ad design for a magazine to promote our online courses. We're a beverage digital newspaper and recently we launched a platform dedicated to tasting courses. Now we want to promote them on a magazine.
The ad must be visually coherent with the website www.scuolaluppolo.it
The headline is "Corsi online sulla birra"
A second text is the following
La proposta didattica di Accademia Malto:
- Corso di degustazione
- Master sulle birre acide
- Master sugli abbinamenti
- Master sulle birre luppolate
- Focus mensili sul movimento italiano
- Esercitazioni pratiche di assaggio
A third text is the following (presented like a claim or tagline):
Con le birre in assaggio spedite direttamente a casa
We also need to promote a coupon with this text:
Usa il coupon GUSTOPIU10 per uno sconto di € 10 sul carrello*
(small text) * Coupon valido per tutto il 2022
Attached is another zip file with platform logo (2 versions) named "Logo Accademia Malto", that we expect big in the page
Our magazine logo is inside a third zip file named "Logo per media" (several versions). We expect it in the lowest part of the page with this text:
Una garanzia
Diario del Calice
(Diario del Calice is the text inside the logo).
The ad design must be a mix of images and texts. A4 size (21 x 29,7 cm) with +0,5 cm of bleed area or, if you prefer, a graphic grid of 18 x 26,4 cm.
We need a source file in PSD format.
Target Market(s)
Beer enthusiasts
Industry/Entity Type
Beer
Font styles to use
Other font styles liked:
- Roboto Slab
Look and feel

```html
<!DOCTYPE html>
<html lang="it">
<head>
<meta charset="utf-8">
<title>Accademia Malto – Corsi online sulla birra</title>
<link href="https://fonts.googleapis.com/css2?family=Roboto+Slab:wght@300;400;500;700;800;900&display=swap" rel="stylesheet">
<style>
  :root{
    --ink:#000000;
    --paper:#ffffff;
    --page:#e9eaec;
    --amber:#fbb40f;
    --amber-deep:#f7a70a;
    --orange:#ef6a33;
    --orange-light:#f48c3e;
    --red:#e8442a;
    --text-dark:#1d1d1d;
    --leaf:#6fbf3a;
  }
  *{margin:0;padding:0;box-sizing:border-box}
  html,body{width:1200px;height:2747px;overflow:hidden}
  body{background:var(--page);font-family:"Roboto Slab",Georgia,serif;position:relative}

  .ad{position:absolute;left:60px;top:611px;width:1080px;height:1525px;background:var(--paper);
      box-shadow:0 20px 50px rgba(0,0,0,.25);overflow:hidden}

  /* hero */
  .hero{position:absolute;left:0;top:0;width:1080px;height:621px;background:var(--ink)}
  .hero-photo{position:absolute;right:0;top:0;width:523px;height:621px;
      background:radial-gradient(ellipse at 60% 45%,#8a6a4c 0%,#4a3a2e 35%,#1b1612 70%,#000 100%)}
  .hero-photo::after{content:"";position:absolute;inset:0;
      background:linear-gradient(90deg,#000 0%,rgba(0,0,0,0) 35%)}
  .brand{position:absolute;left:60px;top:55px;display:flex;align-items:center;gap:20px}
  .brand-mark{width:56px;height:120px;background:var(--amber)}
  .brand-name{color:var(--amber);font-weight:300;font-size:58px;line-height:.98;letter-spacing:3px;text-transform:uppercase}
  .headline{position:absolute;left:55px;top:212px}
  .headline .kicker{display:block;color:var(--amber);font-weight:700;font-size:70px;line-height:1;letter-spacing:-1px}
  .headline .main{display:block;color:var(--paper);font-weight:800;font-size:132px;line-height:.92;margin-top:14px;letter-spacing:-2px}
  .rule{position:absolute;left:0;top:621px;width:1080px;height:14px;background:var(--amber)}

  /* offer list */
  .offer{position:absolute;left:0;top:635px;width:1080px;height:300px;background:var(--paper)}
  .offer h2{position:absolute;left:58px;top:33px;font-weight:500;font-size:33px;color:var(--text-dark);letter-spacing:.3px}
  .offer-list{list-style:none;position:absolute;top:108px;width:520px}
  .offer-list.left{left:58px}
  .offer-list.right{left:452px}
  .offer-list li{display:flex;align-items:center;height:55px;font-size:24px;color:var(--text-dark)}
  .offer-list.left li{gap:24px}
  .offer-list.right li{gap:32px}
  .tick{width:42px;height:42px;flex:none}

  /* shipping + coupon */
  .promo{position:absolute;left:0;top:935px;width:1080px;height:353px}
  .promo-photo{position:absolute;left:0;top:0;width:470px;height:353px;
      background:linear-gradient(120deg,#5d6a78 0%,#2f4f7a 45%,#c9893a 70%,#3a3f46 100%)}
  .promo-panel{position:absolute;left:470px;top:0;width:610px;height:353px;
      background:linear-gradient(135deg,var(--orange-light) 0%,var(--orange) 55%,var(--red) 100%)}
  .claim{position:absolute;left:24px;top:20px;width:528px;height:142px;background:var(--amber);
      padding:14px 24px;font-weight:800;font-size:37px;line-height:1.02;color:var(--text-dark);text-transform:uppercase}
  .coupon{position:absolute;left:36px;top:184px;width:516px;height:153px;display:flex}
  .coupon-label{width:80px;background:var(--paper);border-right:3px dashed var(--red);
      display:flex;align-items:center;justify-content:center;border-radius:14px 0 0 14px}
  .coupon-label span{transform:rotate(-90deg);white-space:nowrap;font-weight:800;font-size:21px;line-height:1;text-align:center;color:var(--text-dark)}
  .coupon-body{width:278px;background:var(--paper);padding:18px 14px 0 14px}
  .coupon-code{font-weight:800;font-size:33px;color:var(--red);line-height:1}
  .coupon-desc{font-weight:800;font-size:21px;color:var(--text-dark);margin-top:3px;letter-spacing:.3px}
  .coupon-note{display:inline-block;margin-top:18px;background:var(--amber);color:var(--text-dark);
      font-weight:700;font-size:11.5px;padding:5px 8px}
  .coupon-value{flex:1;background:var(--ink);border-radius:0 14px 14px 0;color:var(--amber);
      display:flex;flex-direction:column;align-items:center;justify-content:center}
  .coupon-value .amount{font-weight:800;font-size:78px;line-height:.95;letter-spacing:-2px}
  .coupon-value .amount sup{font-size:40px;color:var(--paper);vertical-align:top;position:relative;top:6px;margin-right:2px}
  .coupon-value small{color:var(--paper);font-size:10.5px;font-weight:500;margin-top:4px}

  /* footer */
  .footer{position:absolute;left:0;top:1288px;width:1080px;height:237px;background:var(--ink)}
  .guarantee{position:absolute;left:0;right:0;top:46px;display:flex;justify-content:center;align-items:center;gap:16px}
  .guarantee-label{color:var(--amber);font-weight:800;font-size:40px}
  .media-dot{width:22px;height:22px;border-radius:50%;background:var(--leaf)}
  .media-name{color:#d8d8d8;font-weight:400;font-size:38px}
  .site{position:absolute;left:0;right:0;top:125px;text-align:center;color:var(--paper);font-weight:400;font-size:68px;letter-spacing:.5px}
</style>
</head>
<body>
<main class="ad">
  <section class="hero">
    <div class="hero-photo" role="img" aria-label="Photo of a woman smelling a glass of golden beer"></div>
    <div class="brand">
      <div class="brand-mark"></div>
      <div class="brand-name">Accademia<br>Malto</div>
    </div>
    <h1 class="headline">
      <span class="kicker">CORSI ONLINE</span>
      <span class="main">SULLA<br>BIRRA</span>
    </h1>
  </section>
  <div class="rule"></div>

  <section class="offer">
    <h2>LA PROPOSTA DIDATTICA DI ACCADEMIA MALTO:</h2>
    <ul class="offer-list left">
      <li><svg class="tick" viewBox="0 0 42 42"><circle cx="21" cy="21" r="21" fill="#fbb40f"/><circle cx="21" cy="21" r="11" fill="none" stroke="#1d1d1d" stroke-width="2.5"/><path d="M16 21l4 4 6-7" fill="none" stroke="#1d1d1d" stroke-width="2.8" stroke-linecap="round" stroke-linejoin="round"/></svg>Corso di degustazione</li>
      <li><svg class="tick" viewBox="0 0 42 42"><circle cx="21" cy="21" r="21" fill="#fbb40f"/><circle cx="21" cy="21" r="11" fill="none" stroke="#1d1d1d" stroke-width="2.5"/><path d="M16 21l4 4 6-7" fill="none" stroke="#1d1d1d" stroke-width="2.8" stroke-linecap="round" stroke-linejoin="round"/></svg>Master sulle birre acide</li>
      <li><svg class="tick" viewBox="0 0 42 42"><circle cx="21" cy="21" r="21" fill="#fbb40f"/><circle cx="21" cy="21" r="11" fill="none" stroke="#1d1d1d" stroke-width="2.5"/><path d="M16 21l4 4 6-7" fill="none" stroke="#1d1d1d" stroke-width="2.8" stroke-linecap="round" stroke-linejoin="round"/></svg>Master sugli abbinamenti</li>
    </ul>
    <ul class="offer-list right">
      <li><svg class="tick" viewBox="0 0 42 42"><circle cx="21" cy="21" r="21" fill="#fbb40f"/><circle cx="21" cy="21" r="11" fill="none" stroke="#1d1d1d" stroke-width="2.5"/><path d="M16 21l4 4 6-7" fill="none" stroke="#1d1d1d" stroke-width="2.8" stroke-linecap="round" stroke-linejoin="round"/></svg>Master sulle birre luppolate</li>
      <li><svg class="tick" viewBox="0 0 42 42"><circle cx="21" cy="21" r="21" fill="#fbb40f"/><circle cx="21" cy="21" r="11" fill="none" stroke="#1d1d1d" stroke-width="2.5"/><path d="M16 21l4 4 6-7" fill="none" stroke="#1d1d1d" stroke-width="2.8" stroke-linecap="round" stroke-linejoin="round"/></svg>Focus mensili sul movimento italiano</li>
      <li><svg class="tick" viewBox="0 0 42 42"><circle cx="21" cy="21" r="21" fill="#fbb40f"/><circle cx="21" cy="21" r="11" fill="none" stroke="#1d1d1d" stroke-width="2.5"/><path d="M16 21l4 4 6-7" fill="none" stroke="#1d1d1d" stroke-width="2.8" stroke-linecap="round" stroke-linejoin="round"/></svg>Esercitazioni pratiche di assaggio</li>
    </ul>
  </section>

  <section class="promo">
    <div class="promo-photo" role="img" aria-label="Photo of a bearded brewer in a denim shirt holding up a glass of beer in a brewery"></div>
    <div class="promo-panel">
      <p class="claim">Con le birre in<br>assaggio spedite<br>direttamente a casa</p>
      <div class="coupon">
        <div class="coupon-label"><span>USA IL<br>COUPON</span></div>
        <div class="coupon-body">
          <div class="coupon-code">GUSTOPIU10</div>
          <div class="coupon-desc">PER UNO SCONTO DI</div>
          <span class="coupon-note">* COUPON VALIDO PER TUTTO IL 2022</span>
        </div>
        <div class="coupon-value">
          <div class="amount"><sup>€</sup>10</div>
          <small>SUL CARRELLO*</small>
        </div>
      </div>
    </div>
  </section>

  <footer class="footer">
    <div class="guarantee">
      <span class="guarantee-label">UNA GARANZIA</span>
      <span class="media-dot"></span>
      <span class="media-name">Diario del Calice</span>
    </div>
    <div class="site">www.scuolaluppolo.it</div>
  </footer>
</main>
</body>
</html>
```